Design website for new email startup

We are starting a company called Pingo.QZ (it will live at http://pingo.qz).

We would like the main landing page for our site designed. We have provided a very simple wireframe to help provide direction for the content it should include, but we do not expect the designers to adhere to it at all - we encourage unique ideas. There is some sample text in the wireframe - this does not have to be used, but may provide ideas.

We provide an easy way for people to manage email for a custom domain name. For example if you own "yourhouseword.example" you can point your DNS records to us and we'll make it easy to have emails addressed to your domain get forwarded to your existing email (gmail, etc). Folks running blogs, and other small sites can quickly setup email addresses for their domains and manage them in one place.

(For technical folks, we have you point your dns mx records to us, hence the name. That way all your email hits us and we can redirect it wherever you want. We make it easy to manage a single domain or a bunch of domains. Many domain registrars offer this service for a fee, and have clumsy management tools. We provide a robust simple toolset for free, as well as premium options).

The goal of the landing page is to get folks into the signup flow. The second priority flow is to have them take a look at the premium plan offerings.

We may offer the winning designer additional work for the remainder of the site design.
Updates

I've changed this project to a committed payment.  It is no longer refundable.  Thank you.

Target Market(s)

Bloggers, podcasters, designers, app developers - people who are a little tech savvy.

Industry/Entity Type

It Company

Font styles to use
Sans Serif

Colors

Designer to choose colors to be used in the design.

Requirements
Must have
• A full fidelity mockup (comp) of the landing page including the source file (psd, ai, etc).

Some sort of logo treatment for the pingo.qz brand

A call to action for signup, such as the suggested 'Get Started Here'
Nice to have
• A hip startup feel

Incorporation of the email theme

Give the impression it is simple, easy and fast

```html
<!DOCTYPE html>
<html lang="en">
<head>
<meta charset="utf-8">
<title>Pingo.QZ – We make email easy</title>
<link rel="stylesheet" href="https://fonts.googleapis.com/css2?family=Oswald:wght@400;500;600&family=Arimo:wght@400;700&display=swap">
<style>
  :root {
    --orange-light: #ffa33a;
    --orange: #ff7f0a;
    --orange-deep: #f06a00;
    --ink: #111111;
    --white: #ffffff;
    --page: #ffffff;
    --card-bg: #f2f2f2;
    --card-border: #c9c9c9;
    --tile-light: #f4f4f4;
    --tile-dark: #c8c8c8;
    --hero-dark: #1f2a33;
    --hero-mid: #34434e;
    --hero-glow: #cfd6da;
    --footer-top: #4a4c4f;
    --footer-bottom: #232426;
    --arrow-bg: #dcdcdc;
    --arrow-ink: #555555;
    --social: #d8d8d8;
  }
  * { box-sizing: border-box; margin: 0; padding: 0; }
  html, body { width: 1200px; height: 539px; overflow: hidden; background: var(--page); }
  body { position: relative; font-family: "Arimo", Arial, sans-serif; }

  .site-header {
    position: absolute; left: 238px; top: 0; width: 724px; height: 62px;
    background: linear-gradient(var(--orange-light), var(--orange) 70%, var(--orange-deep));
  }
  .brand {
    position: absolute; left: 36px; top: 14px;
    font-family: "Oswald", sans-serif; font-weight: 500; font-size: 29px; line-height: 1;
    color: var(--white); letter-spacing: 0.5px;
  }
  .phone {
    position: absolute; right: 20px; top: 15px;
    display: flex; align-items: center; gap: 8px;
    font-family: "Arimo", sans-serif; font-weight: 700; font-size: 12px; color: var(--white);
  }
  .phone svg { width: 13px; height: 14px; }
  .top-nav {
    position: absolute; right: 20px; top: 42px;
    font-weight: 700; font-size: 11px; color: var(--white); word-spacing: 1px;
  }
  .top-nav span.sep { margin: 0 9px; }

  .slider-arrow {
    position: absolute; top: 167px; width: 44px; height: 44px; border-radius: 50%;
    background: var(--arrow-bg); color: var(--arrow-ink);
    font-family: "Arimo", sans-serif; font-weight: 700; font-size: 22px;
    display: flex; align-items: center;
  }
  .slider-arrow.prev { left: 217px; padding-left: 5px; }
  .slider-arrow.next { left: 940px; justify-content: flex-end; padding-right: 5px; }

  .hero {
    position: absolute; left: 239px; top: 69px; width: 723px; height: 255px; overflow: hidden;
  }
  .hero-visual {
    position: absolute; inset: 0;
    background:
      radial-gradient(ellipse 180px 150px at 500px 95px, var(--hero-glow), transparent 75%),
      linear-gradient(90deg, var(--hero-dark) 0%, var(--hero-mid) 55%, #55656f 75%, var(--hero-dark) 100%);
  }
  .hero-title {
    position: absolute; left: 63px; top: 103px;
    font-family: "Oswald", sans-serif; font-weight: 500; font-size: 22px; line-height: 1;
    color: var(--white); letter-spacing: 1.5px;
  }
  .btn {
    position: absolute; top: 150px; width: 151px; height: 31px; border-radius: 2px;
    display: flex; align-items: center; justify-content: center;
    font-weight: 700; font-size: 12px; color: var(--white); letter-spacing: 0.4px;
    text-shadow: 0 1px 1px rgba(0,0,0,0.45);
  }
  .btn-primary { left: 25px; background: linear-gradient(var(--orange-light), var(--orange-deep)); }
  .btn-secondary { left: 186px; background: linear-gradient(#4a4a4a, #0e0e0e); }

  .guide-card {
    position: absolute; top: 336px; width: 345px; height: 122px;
    background: var(--card-bg); border: 1px solid var(--card-border);
  }
  .guide-card.dns { left: 239px; }
  .guide-card.registrar { left: 615px; }
  .partner-tile {
    position: absolute; left: 14px; top: 7px; width: 120px; height: 99px; border-radius: 4px;
    background: radial-gradient(circle at 50% 45%, var(--tile-light), var(--tile-dark));
    display: flex; align-items: center; justify-content: center;
    font-weight: 700; font-size: 17px; color: var(--ink);
  }
  .guide-text {
    position: absolute; left: 159px; top: 17px; width: 180px;
    font-size: 11px; line-height: 16px; color: var(--ink); text-transform: uppercase;
  }
  .guide-card.registrar .guide-text { left: 142px; top: 17px; width: 200px; }
  .btn-details {
    position: absolute; left: 158px; top: 75px; width: 81px; height: 16px; border-radius: 2px;
    background: linear-gradient(var(--orange-light), var(--orange-deep));
    font-size: 10.5px; line-height: 16px; text-align: center; color: var(--ink);
  }
  .guide-card.registrar .btn-details { left: 142px; top: 79px; }

  .site-footer {
    position: absolute; left: 239px; top: 469px; width: 724px; height: 70px;
    background: linear-gradient(var(--footer-top), var(--footer-bottom));
    color: var(--white);
  }
  .footer-nav { position: absolute; left: 24px; top: 20px; font-size: 11px; }
  .footer-nav span.sep { margin: 0 9px; }
  .copyright { position: absolute; left: 24px; top: 47px; font-size: 9px; color: #dddddd; }
  .social { position: absolute; left: 614px; top: 15px; display: flex; gap: 4px; }
  .social span { width: 23px; height: 23px; border-radius: 50%; background: var(--social); }
  .rights { position: absolute; left: 610px; top: 49px; font-size: 9px; color: #dddddd; }
</style>
</head>
<body>
  <header class="site-header">
    <div class="brand">PINGO.QZ</div>
    <div class="phone">
      <svg viewBox="0 0 13 14" aria-hidden="true"><path d="M2.5 0.5 L5 3.2 L3.6 5 C4.4 7 6 8.8 8 9.8 L9.8 8.4 L12.5 10.8 L11 13 C5.5 13 0.5 7.5 0.5 2.2 Z" fill="#333"/></svg>
      00-5550-1234-77
    </div>
    <nav class="top-nav">HOW IT WORKS<span class="sep">|</span>SUPPORT<span class="sep">|</span>LOGIN</nav>
  </header>

  <div class="slider-arrow prev">&#10094;</div>
  <div class="slider-arrow next">&#10095;</div>

  <section class="hero">
    <div class="hero-visual" role="img" aria-label="World map backdrop with a hand touching a glowing open envelope bearing an at-sign"></div>
    <h1 class="hero-title">WE MAKE EMAIL EASY</h1>
    <div class="btn btn-primary">GET STARTED FREE</div>
    <div class="btn btn-secondary">COMPARE PLANS</div>
  </section>

  <article class="guide-card dns">
    <div class="partner-tile">SkyVeil</div>
    <p class="guide-text">How to configure<br>your SkyVeil DNS to<br>use Pingo.QZ</p>
    <div class="btn-details">More Details</div>
  </article>

  <article class="guide-card registrar">
    <div class="partner-tile">DomainDen</div>
    <p class="guide-text">Use Pingo.QZ with yourr<br>DomainDen domain registration<br>for reliable email forwarding</p>
    <div class="btn-details">More Details</div>
  </article>

  <footer class="site-footer">
    <nav class="footer-nav">HOW IT WORKS<span class="sep">|</span>SUPPORT<span class="sep">|</span>LOGIN</nav>
    <p class="copyright">Copyrights © 2014 pingo.qz.com.</p>
    <div class="social"><span></span><span></span><span></span></div>
    <p class="rights">All rights reserved</p>
  </footer>
</body>
</html>
```